Verodex business card

Business card for sustainable investment company called "Verodex". Verodex is an exchange platform selling carbon credits between buyers and sellers. Carbon Credits are an environmental commodity for reducing global carbon emissions.

the card should obviously have our logo and the theme should be sustainability/environment mixed with a trading platform.

Contact Information for Business Card

Logo, Name, Title, Phone, Email

Colors
0054AA
0677BA
7BADD7
CADEEF
E8F1F8
0094D4
00A9DD
6FCCEA
C7EBF8
E9F6FB
00AB8E
00BBA5
67D7C9
C6EFE9
E9F9F6
59FF00
82FF00
B8FF75
E3FFCB
F4FFEA

```html
<!DOCTYPE html>
<html lang="en">
<head>
<meta charset="utf-8">
<title>Verodex business card</title>
<link href="https://fonts.googleapis.com/css2?family=Archivo:wght@400;600;700&display=swap" rel="stylesheet">
<style>
  :root {
    --stage: #e9edf1;
    --card-white: #fbfbfb;
    --navy: #0a2a66;
    --navy-deep: #06204f;
    --brand-blue: #0677ba;
    --bright-blue: #1e8fe0;
    --sky: #00a9dd;
    --ink: #1c2430;
    --grey-text: #4a5360;
    --rule: #3c5a8a;
  }
  * { box-sizing: border-box; margin: 0; padding: 0; }
  html, body { width: 1200px; height: 800px; overflow: hidden; }
  body {
    background: var(--stage);
    font-family: "Archivo", Arial, sans-serif;
    display: flex;
    align-items: center;
    justify-content: center;
    gap: 80px;
  }
  .card {
    width: 340px;
    height: 560px;
    border-radius: 22px;
    position: relative;
    box-shadow: 0 10px 30px rgba(10, 30, 60, 0.18);
    overflow: hidden;
  }
  .card-front {
    background: var(--card-white);
    display: flex;
    flex-direction: column;
    align-items: center;
  }
  .brand {
    margin-top: 92px;
    display: flex;
    align-items: center;
    gap: 12px;
  }
  .brand-square {
    width: 30px;
    height: 30px;
    background: var(--sky);
  }
  .brand-name {
    font-weight: 700;
    font-size: 30px;
    letter-spacing: 1px;
    color: var(--ink);
    text-transform: uppercase;
  }
  .person {
    margin-top: 150px;
    text-align: center;
  }
  .person-name {
    font-weight: 700;
    font-size: 21px;
    color: var(--bright-blue);
    letter-spacing: 0.5px;
  }
  .person-title {
    font-size: 12px;
    color: var(--grey-text);
    margin-top: 2px;
  }
  .icon-row {
    margin-top: 10px;
    display: flex;
    align-items: center;
    gap: 6px;
  }
  .icon-row .rule {
    width: 40px;
    height: 1px;
    background: var(--rule);
  }
  .icon {
    width: 20px;
    height: 20px;
    border-radius: 4px;
    background: linear-gradient(180deg, #2ea6ee, var(--brand-blue));
    display: flex;
    align-items: center;
    justify-content: center;
  }
  .contacts {
    margin-top: 10px;
    text-align: center;
    font-size: 13px;
    line-height: 1.35;
    color: var(--grey-text);
  }
  .divider {
    width: 150px;
    height: 1px;
    background: var(--rule);
    margin: 14px 0 12px;
  }
  .address {
    text-align: center;
    font-size: 13px;
    line-height: 1.35;
    color: var(--grey-text);
  }
  .card-back {
    background: var(--navy);
  }
  .back-pattern {
    position: absolute;
    inset: 0;
    background: linear-gradient(160deg, var(--navy-deep), var(--navy) 55%, #0e3a80);
  }
  .back-brand {
    position: absolute;
    right: 28px;
    bottom: 200px;
    display: flex;
    align-items: center;
    gap: 8px;
  }
  .back-brand .brand-square { width: 16px; height: 16px; }
  .back-brand .brand-name { font-size: 18px; color: var(--sky); }
</style>
</head>
<body>
  <section class="card card-front">
    <div class="brand">
      <span class="brand-square"></span>
      <span class="brand-name">Verodex</span>
    </div>

    <div class="person">
      <p class="person-name">DANIEL MORROW</p>
      <p class="person-title">Managing Director</p>
    </div>

    <div class="icon-row">
      <span class="rule"></span>
      <span class="icon" aria-label="Phone">
        <svg width="12" height="12" viewBox="0 0 24 24"><path fill="#fff" d="M6.6 10.8a15.1 15.1 0 0 0 6.6 6.6l2.2-2.2c.3-.3.7-.4 1-.2 1.1.4 2.3.6 3.6.6.6 0 1 .4 1 1V20c0 .6-.4 1-1 1A17 17 0 0 1 3 4c0-.6.4-1 1-1h3.5c.6 0 1 .4 1 1 0 1.3.2 2.5.6 3.6.1.3 0 .7-.2 1z"/></svg>
      </span>
      <span class="icon" aria-label="Email">
        <svg width="12" height="12" viewBox="0 0 24 24"><rect x="2" y="5" width="20" height="14" rx="2" fill="#fff"/><path d="M3 6l9 7 9-7" stroke="#0677ba" stroke-width="2" fill="none"/></svg>
      </span>
      <span class="icon" aria-label="Website">
        <svg width="12" height="12" viewBox="0 0 24 24"><circle cx="12" cy="12" r="9" fill="none" stroke="#fff" stroke-width="2"/><ellipse cx="12" cy="12" rx="4" ry="9" fill="none" stroke="#fff" stroke-width="2"/><path d="M3 12h18" stroke="#fff" stroke-width="2"/></svg>
      </span>
      <span class="rule"></span>
    </div>

    <div class="contacts">
      <p>555-018-2047</p>
      <p>info@verodex.com</p>
      <p>www.verodex.com</p>
    </div>

    <div class="divider"></div>

    <div class="address">
      <p>2196 Willow Crest Road</p>
      <p>Fairbanks, Alaska 99701</p>
    </div>
  </section>

  <section class="card card-back">
    <div class="back-pattern" role="img" aria-label="Repeating embossed brand pattern in deep navy tones"></div>
    <div class="back-brand">
      <span class="brand-square"></span>
      <span class="brand-name">Verodex</span>
    </div>
  </section>
</body>
</html>
```